All Natural Mosquito Repellent

My company, BrightPebble Company has created an all natural mosquito repellent. I already have other all natural products that I have developed and created labels for. I will include a copy of that label so you have something to work from. I will need two labels. One for the front of the bottle and one for the back. The back label will need space for a UPC. The labels need to be 63mm (H) x 39mm (W)

Target Market(s)

Consumers, Organic, People who like natural products

Font styles to use
Other font styles liked:
• A combination of both Serif and Sans Serif

Requirements
Must have
• Use the words Organic, All Natural, Travel size, made in the USA label
Nice to have
• tag line: Don't beat them off. Spray them away.

```html
<!DOCTYPE html>
<html lang="en">
<head>
<meta charset="utf-8">
<title>BrightPebble Company – Mosquito Repellent Labels</title>
<link rel="stylesheet" href="https://fonts.googleapis.com/css2?family=Oswald:wght@500;600&family=Open+Sans:wght@400;600;700&family=Allura&display=swap">
<style>
  :root{
    --page:#ffffff;
    --forest:#0c3a0a;
    --forest-deep:#062a06;
    --tree:#1f5a14;
    --sun-top:#f68a1f;
    --sun-mid:#f9b233;
    --sun-glow:#fbe27a;
    --rust:#b9502a;
    --script:#c9481e;
    --ink:#3b3b3b;
    --white:#ffffff;
  }
  *{box-sizing:border-box;margin:0;padding:0}
  html,body{width:1200px;height:1200px;overflow:hidden;background:var(--page)}
  .sheet{position:relative;width:1200px;height:1200px;display:flex;justify-content:center;align-items:center;gap:90px}
  .label{position:relative;width:470px;height:760px;border-radius:12px;overflow:hidden}

  /* front */
  .front{background:var(--forest)}
  .front .sky{position:absolute;left:0;top:0;width:100%;height:300px;
    background:radial-gradient(ellipse 70% 85% at 50% 100%,var(--sun-glow) 0%,var(--sun-mid) 45%,var(--sun-top) 100%)}
  .brand{position:absolute;top:120px;width:100%;text-align:center}
  .brand-name{font-family:"Open Sans",sans-serif;font-weight:600;font-size:27px;color:var(--ink);letter-spacing:.5px}
  .brand-dot{display:inline-block;width:40px;height:40px;border-radius:50%;background:var(--ink);margin-bottom:12px}
  .brand-sub{font-family:"Open Sans",sans-serif;font-size:10.5px;color:var(--ink);margin-top:4px;word-spacing:2px}
  .treeline{position:absolute;left:0;top:215px;width:100%;height:95px;
    background:linear-gradient(to bottom,rgba(31,90,20,0) 0%,var(--tree) 45%,var(--forest) 100%)}
  .features{position:absolute;top:290px;width:100%;text-align:center;font-family:"Oswald",sans-serif;font-weight:500;
    font-size:16px;color:var(--white);letter-spacing:.2px}
  .features .sep{display:inline-block;width:9px;height:9px;border-radius:50%;background:var(--white);margin:0 10px 2px}
  .product{position:absolute;left:55px;top:315px;width:350px;height:65px;background:var(--rust);border-radius:3px;
    display:flex;align-items:center;justify-content:center;font-family:"Oswald",sans-serif;font-weight:600;font-size:38px;color:var(--white);letter-spacing:.3px}
  .tagline{position:absolute;top:395px;width:100%;text-align:center;font-family:"Oswald",sans-serif;font-weight:500;font-style:italic;
    font-size:36px;line-height:46px;color:var(--white)}
  .promise{position:absolute;top:500px;width:100%;text-align:center;font-family:"Allura",cursive;font-size:26px;color:var(--script)}
  .ground{position:absolute;left:0;bottom:0;width:100%;height:110px}
  .shield{position:absolute;left:188px;top:568px;width:102px;height:112px}
  .made{position:absolute;bottom:20px;left:140px;font-family:"Open Sans",sans-serif;font-size:22px;color:var(--white)}
  .volume{position:absolute;bottom:22px;right:35px;font-family:"Oswald",sans-serif;font-weight:600;font-size:16px;color:var(--white)}

  /* back */
  .back{background:var(--forest);color:var(--white);font-family:"Open Sans",sans-serif;text-align:center;padding:48px 28px 0}
  .back h2{font-size:14.5px;font-weight:700;margin-bottom:16px}
  .back p{font-size:10.3px;line-height:15.5px;margin:0 auto 28px}
  .back .wide{width:400px}
  .back .mid{width:375px}
  .back .narrow{width:300px}
  .address h2{font-size:18px;font-weight:600;margin-bottom:8px}
  .address p{font-size:15px;line-height:20px;width:270px;text-align:left;margin:0 auto}
  .recycle{position:absolute;left:30px;bottom:72px;width:62px;height:62px}
  .upc{position:absolute;left:120px;bottom:42px;width:318px;height:95px;border:2px solid var(--white);
    display:flex;align-items:center;justify-content:center;font-size:32px;font-weight:600}
</style>
</head>
<body>
<main class="sheet">

  <section class="label front">
    <div class="sky"></div>
    <div class="brand">
      <span class="brand-dot"></span>
      <div class="brand-name">BrightPebble Company</div>
      <div class="brand-sub">crafted by hand, with love&nbsp;&nbsp;&nbsp;&nbsp;&nbsp;&nbsp;in the U.S.A.</div>
    </div>
    <div class="treeline" role="img" aria-label="Silhouette of a pine forest along the horizon"></div>
    <div class="features">ALL NATURAL<span class="sep"></span>ORGANIC<span class="sep"></span>TRAVEL SIZE</div>
    <div class="product">MOSQUITO REPELLENT</div>
    <div class="tagline">“Don't beat them off<br>Spray them away”</div>
    <div class="promise">Long lasting protection</div>
    <svg class="ground" viewBox="0 0 470 110" preserveAspectRatio="none">
      <path d="M0 50 Q235 -25 470 50 L470 110 L0 110Z" fill="var(--forest-deep)"/>
      <path d="M0 50 Q235 -25 470 50" fill="none" stroke="#c9c9c9" stroke-width="2"/>
    </svg>
    <svg class="shield" viewBox="0 0 102 112" role="img" aria-label="Shield emblem with a mosquito">
      <path d="M4 8 Q51 -4 98 8 L96 60 Q90 92 51 108 Q12 92 6 60Z" fill="var(--white)" stroke="#bdbdbd" stroke-width="3"/>
    </svg>
    <div class="made">Made in the USA</div>
    <div class="volume">50 ML</div>
  </section>

  <section class="label back">
    <h2>DIRECTION FOR USE:</h2>
    <p class="wide">There are many variations of passages of Lorem Ipsum available, but the majority have suffered alteration in some form, by injected humour, or randomised words which don't look even slightly believable. If you are going to use a passage of Lorem Ipsum, you need to be sure there isn't anything embarrassing hidden in the middle of text.</p>
    <h2>PRECAUTION:</h2>
    <p class="mid">There are many variations of passages of Lorem Ipsum available, but the majority have suffered alteration in some form, by injected humour, or randomised words which don't look even slightly believable.</p>
    <h2>INGREDIENTS:</h2>
    <p class="mid">There are many variations of passages of Lorem Ipsum available, but the majority have suffered alteration in some form, by injected humour, or randomised words which don't look even slightly believable.</p>
    <h2>STORAGE:</h2>
    <p class="narrow">Store in a cool and dry place. Place empty container in trsh or recycle.</p>
    <div class="address">
      <h2>Company Address:</h2>
      <p>Lorem Ipsum is simply dummy text of the printing and typesetting industry.</p>
    </div>
    <svg class="recycle" viewBox="0 0 62 62" role="img" aria-label="Recycling symbol">
      <circle cx="31" cy="31" r="26" fill="#000000"/>
    </svg>
    <div class="upc">UPC</div>
  </section>

</main>
</body>
</html>
```